Help our Sugar Loom find our winning design! We're looking for a business card....

We’re a Sugar Loom in NY specializing in custom-made cakes and unique desserts.
Our cakes combine flavor and art, each designed to match customer’s special event and theme.
We’d like a unique business card with a clean design that will combine French chic and artistic look & feel.
We’d like to differentiate ourselves from standard bakeries, please don’t offer cupcake images :-)
Our logo is peach-pink and brown and we’d love to use these colors ( . Another color that can be added is gold - or feel free to suggest!

Target Market(s)

Women, ages 25-55

Industry/Entity Type

Boutique

Contact Information for Business Card

Text on card:
Logo
Sugar Loom by Dana Welch

www.sugarloomsweets.com
hello@sugarloom.com
(516) 555-0147
F – sugarloomnyc
IG - sugarloom_ny

Font styles to use
Sans Serif
Script

Requirements
Must have
• Logo
• Clean look
• French chic and artistic look & feel.
Nice to have
• Damask pattern
Should not have
• Cupcake images

```html
<!DOCTYPE html>
<html lang="en">
<head>
<meta charset="utf-8">
<title>Sugar Loom – Business Card</title>
<link href="https://fonts.googleapis.com/css2?family=Exo+2:wght@400;500;600&display=swap" rel="stylesheet">
<style>
  :root {
    --stage: #2b2a29;
    --card: #f4f4f4;
    --card-edge: #e2e2e2;
    --charcoal: #545252;
    --pink: #f28fa2;
    --ink: #2f2f2f;
    --white: #ffffff;
  }
  * { box-sizing: border-box; margin: 0; padding: 0; }
  html, body {
    width: 1200px; height: 899px; overflow: hidden;
    background: var(--stage);
    font-family: "Exo 2", "Helvetica Neue", Arial, sans-serif;
  }
  .canvas { position: relative; width: 1200px; height: 899px; }
  .card {
    position: absolute; left: 250px; width: 700px; height: 400px;
    background: radial-gradient(ellipse at 45% 55%, var(--white) 0%, var(--card) 60%, var(--card-edge) 100%);
    overflow: hidden;
    box-shadow: 0 14px 30px rgba(0,0,0,.45);
  }
  .card--back { top: 30px; }
  .card--front { top: 469px; }

  .brand { display: flex; align-items: center; gap: 10px; color: var(--pink); font-weight: 500; }
  .brand__dot { width: 14px; height: 14px; border-radius: 50%; background: var(--pink); }
  .card--back .brand { position: absolute; left: 0; right: 0; top: 172px; justify-content: center; font-size: 40px; }
  .card--back .brand__dot { width: 18px; height: 18px; }

  .front-shape { position: absolute; inset: 0; width: 700px; height: 400px; }
  .card--front .brand { position: absolute; left: 92px; top: 120px; font-size: 30px; }

  .identity { position: absolute; right: 24px; top: 86px; text-align: right; color: var(--white); }
  .identity__name { font-size: 26px; font-weight: 500; letter-spacing: 1.5px; text-transform: uppercase; }
  .identity__role { font-size: 17px; margin-top: 4px; letter-spacing: .5px; }

  .contacts { position: absolute; left: 34px; top: 228px; list-style: none; color: var(--ink); font-size: 14px; letter-spacing: .6px; }
  .contacts li { display: flex; align-items: center; gap: 10px; height: 25px; }
  .contacts svg { width: 15px; height: 15px; fill: var(--ink); flex: none; }

  .address { position: absolute; right: 40px; bottom: 22px; text-align: right; color: var(--ink); font-size: 15px; line-height: 1.55; letter-spacing: .6px; }
</style>
</head>
<body>
<main class="canvas">

  <section class="card card--back" aria-label="Card back">
    <div class="brand"><span class="brand__dot"></span><span>Sugar Loom</span></div>
  </section>

  <section class="card card--front" aria-label="Card front">
    <svg class="front-shape" viewBox="0 0 700 400" aria-hidden="true">
      <path d="M0,0 H700 V400 H690 C652,205 430,46 0,50 Z" fill="var(--charcoal)"/>
      <path d="M0,50 C430,46 652,205 690,400 H676 C640,215 420,62 0,64 Z" fill="var(--card-edge)"/>
      <path d="M0,52 C430,48 652,207 690,400 H672 C636,218 416,66 0,66 Z" fill="var(--pink)"/>
      <path d="M0,62 C418,58 640,214 676,400 H672 C636,218 416,66 0,66 Z" fill="var(--pink)"/>
    </svg>

    <div class="brand"><span class="brand__dot"></span><span>Sugar Loom</span></div>

    <div class="identity">
      <p class="identity__name">Dana Welch</p>
      <p class="identity__role">Managing Director</p>
    </div>

    <ul class="contacts">
      <li><svg viewBox="0 0 16 16"><path d="M3 1h3l1 4-2 1a9 9 0 0 0 5 5l1-2 4 1v3a2 2 0 0 1-2 2A13 13 0 0 1 1 3a2 2 0 0 1 2-2z"/></svg>(516) 555-0147</li>
      <li><svg viewBox="0 0 16 16"><path d="M4 0h8a1 1 0 0 1 1 1v14a1 1 0 0 1-1 1H4a1 1 0 0 1-1-1V1a1 1 0 0 1 1-1zm1 2v10h6V2zm3 11a1 1 0 1 0 0 2 1 1 0 0 0 0-2z"/></svg>(516) 555-0148</li>
      <li><svg viewBox="0 0 16 16"><path d="M4 0h6v5H4zM1 6h14v9H1zm3 3v2h2V9zm4 0v2h2V9zm4-1v5h2V8z"/></svg>(516) 555-0149</li>
      <li><svg viewBox="0 0 16 16"><path d="M0 3h16v10H0zm1.5 1.2L8 9l6.5-4.8V4h-13z"/></svg>hello@sugarloom.com</li>
      <li><svg viewBox="0 0 16 16"><path d="M8 0a8 8 0 1 0 0 16A8 8 0 0 0 8 0zm5.9 7h-2.5a12 12 0 0 0-1.2-4.7A6 6 0 0 1 13.9 7zM8 2c.8 1 1.4 2.8 1.5 5h-3C6.6 4.8 7.2 3 8 2zM5.8 2.3A12 12 0 0 0 4.6 7H2.1a6 6 0 0 1 3.7-4.7zM2.1 9h2.5a12 12 0 0 0 1.2 4.7A6 6 0 0 1 2.1 9zM8 14c-.8-1-1.4-2.8-1.5-5h3c-.1 2.2-.7 4-1.5 5zm2.2-.3A12 12 0 0 0 11.4 9h2.5a6 6 0 0 1-3.7 4.7z"/></svg>www.sugarloomsweets.com</li>
    </ul>

    <p class="address">214 Mott Street,<br>New York NY</p>
  </section>

</main>
</body>
</html>
```